Employment Agency Website Design

We are working with an employment agency in California.

Some sites to use for content/competitors and inspiration:

https://www.pinecrestjobs.com/us/en
https://www.velmorusa.com
https://www.dravenworks.us
https://www.quillora.com/en
https://www.tomvalusa.com
https://www.fernstaffing.com

Thank you for taking the time to consider designing a website for us. We are web developers based in Stockton, CA, USA. Most of our projects go through the same process. Understanding this process may help you win a project with us. We custom-code all of our websites in-house. We don’t have any requirements as to what tools you use for your design, but we prefer Figma files. For any design that we label as four-stars, we send it to the client for review. The client picks the final design they want us to use. Once we complete this process, we will continue to show additional clients all the four-star sites and purchase them later. Your designs will have multiple chances to sell. For better chances of success, we ask that you follow these guidelines.

IMAGES:
If you use any images or icons in the design, we ask that you have a link to the asset so we can purchase the image/icon. Most of the designs we submit do not have the customer’s images on them unless they have some great images. Be creative; show us the feeling you are trying to portray with your image choices. Use any royalty-free site you choose. We subscribe to Adobe and mainly use their images, but we can purchase images outside of Adobe. PLEASE NOTE: we will not submit designs to clients with watermarks on the images.

FONTS:
We ask that you identify the fonts used in the design. This can be done in a message if you want. We typically use Google Fonts and Adobe Fonts.

CONTENT:
We're always open to different content and ideas. We often submit designs with stock images so the client can see our vision. We typically take pictures after the website launch to use their images with our vision. Lorem Ipsum is fine for paragraphs, but we ask that you write the headers in correct English. We want to be able to show the vision and identify the sections of the website.

INSPIRATION:
We typically add a couple of links in the brief of websites we like to help you get started in your design.

REVISIONS:
We do not often ask for revisions of the designs unless we see something in the design that may not appeal to the client. If there are slight changes that we want to make, we do that in the development process.

FEEDBACK:
We rarely give feedback on designs during the design process. We are working on many website projects and do not have the time to provide feedback. We usually respond if your request is well thought out and asks specific questions, but a note asking “feedback, please” usually goes unanswered.

```html
<!DOCTYPE html>
<html lang="en">
<head>
<meta charset="utf-8">
<title>Brightpath — Find Jobs and Hire Talent</title>
<link rel="stylesheet" href="https://fonts.googleapis.com/css2?family=Fira+Sans:wght@400;500;600&family=Inter:wght@400;500;600;700&display=swap">
<style>
:root{
  --red:#c01e2e;
  --ink:#1d1d1f;
  --muted:#555;
  --line:#d9d9d9;
  --gray-band:#efeff1;
  --white:#fff;
}
*{box-sizing:border-box;margin:0;padding:0}
html,body{width:1200px;height:4038px;overflow:hidden}
body{position:relative;font-family:"Inter",sans-serif;color:var(--ink);background:var(--white)}
.abs{position:absolute}
.heading{font-family:"Fira Sans",sans-serif;font-weight:400;letter-spacing:.5px}

/* header */
.site-header{position:absolute;left:0;top:0;width:1200px;height:92px}
.brand{position:absolute;left:28px;top:27px;display:flex;align-items:center;gap:10px}
.brand-mark{width:26px;height:26px;background:var(--red)}
.brand-name{font-size:24px;font-weight:600;color:var(--ink);line-height:1}
.main-nav{position:absolute;top:36px;left:457px;display:flex;gap:26px;font-size:14px;font-weight:500}
.login{position:absolute;left:1084px;top:29px;width:76px;height:30px;border:1.5px solid #333;border-radius:3px;font-size:14px;font-weight:500;display:flex;align-items:center;justify-content:center}

/* hero */
.hero{position:absolute;left:0;top:92px;width:1200px;height:586px;background:linear-gradient(100deg,#5a3a2a 0%,#b56a3a 30%,#7d6a60 60%,#a9a39c 100%)}
.hero-title{position:absolute;left:34px;top:316px;font-size:44px;font-weight:500;color:#fff}
.hero-label{position:absolute;top:390px;font-size:19px;color:#fff}
.hero-input{position:absolute;top:428px;height:58px;background:#fff;border-radius:3px;padding:0 16px;font-size:19px;color:#aaa;display:flex;align-items:center}
.hero-btn{position:absolute;left:720px;top:428px;width:151px;height:58px;background:var(--red);color:#fff;font-size:19px;font-weight:600;display:flex;align-items:center;justify-content:center;border-radius:3px}
.hero-opt{position:absolute;top:497px;font-size:19px;color:#fff;display:flex;align-items:center;gap:12px}
.checkbox{width:22px;height:22px;background:#fff;border-radius:3px}

/* tabs */
.tabs{position:absolute;top:718px;left:273px;display:flex;gap:42px;font-size:14px;font-weight:600}
.tabs span{border-bottom:1.5px solid #999;padding-bottom:6px}

/* industry list */
.industry{position:absolute;display:flex;align-items:center;font-size:15px;width:300px}
.industry .ic{width:22px;height:20px;background:var(--red);border-radius:3px;margin-right:12px;flex:none}
.industry .txt{border-bottom:1px solid var(--line);padding-bottom:3px;width:240px;white-space:nowrap}

/* how it works */
.how-title{position:absolute;left:0;width:1200px;top:1024px;text-align:center;font-size:42px;color:#333}
.step{position:absolute;top:1136px;height:86px;border:1.5px solid #bbb;background:#fff;display:flex;align-items:center;padding-left:34px;font-size:20px;font-weight:600;line-height:1.2}
.step-num{position:absolute;top:1117px;width:38px;height:38px;border-radius:50%;background:var(--red);color:#fff;font-size:22px;display:flex;align-items:center;justify-content:center}
.connector{position:absolute;top:1178px;height:1.5px;background:#bbb}

/* latest jobs */
.jobs-band{position:absolute;left:0;top:1299px;width:1200px;height:652px;background:var(--gray-band)}
.jobs-title{position:absolute;left:41px;top:1332px;font-size:42px;color:#333}
.job-card{position:absolute;top:1418px;width:356px;height:410px;background:#fff;border:1.5px solid #d5d5d5}
.job-added{position:absolute;left:10px;top:8px;font-size:12px;color:#555}
.job-title{position:absolute;left:0;width:100%;top:38px;text-align:center;color:var(--red);font-size:23px;font-weight:600}
.job-desc{position:absolute;left:31px;right:31px;top:87px;font-size:19px;line-height:24px;text-align:justify}
.job-meta{position:absolute;left:31px;font-size:14px;display:flex;align-items:center;gap:8px}
.job-btn{position:absolute;left:31px;top:330px;width:244px;height:42px;background:var(--red);color:#fff;font-size:19px;display:flex;align-items:center;justify-content:center}
.bookmark{position:absolute;left:290px;top:332px}
.see-more{position:absolute;left:41px;top:1862px;font-size:26px;font-weight:700;color:var(--red)}

/* red feature bands */
.red-band{position:absolute;left:0;width:1200px;background:var(--red)}
.frame{position:absolute;background:#fff}
.photo{position:absolute}
.feature-title{position:absolute;font-size:42px;color:#fff;line-height:47px}
.check-item{position:absolute;display:flex;gap:14px;font-size:19px;line-height:24px;color:#fff}
.check-item svg{flex:none}
.btn-white{position:absolute;height:60px;background:#fff;color:var(--red);font-weight:600;display:flex;align-items:center;justify-content:center;text-align:center;line-height:22px}

/* insights */
.insights-title{position:absolute;left:82px;top:3128px;font-size:42px;color:#333}
.insight{position:absolute;top:3230px;width:272px;height:450px;background:#fff;box-shadow:0 2px 6px rgba(0,0,0,.15)}
.insight .photo{left:7px;top:20px;width:248px;height:186px}
.insight h3{position:absolute;left:7px;right:18px;top:235px;font-size:20px;font-weight:600;color:var(--red);line-height:24px}
.insight p{position:absolute;left:7px;right:14px;top:300px;font-size:19px;line-height:24px;text-align:justify}
.insight .read{position:absolute;left:7px;top:382px;width:152px;height:50px;background:var(--red);color:#fff;font-size:19px;font-weight:600;display:flex;align-items:center;justify-content:center}

/* footer */
.footer-line{position:absolute;left:0;top:3726px;width:1200px;height:1.5px;background:#d58a92}
.footer-brand{position:absolute;left:106px;top:3830px;width:180px;text-align:center}
.footer-brand .brand-mark{width:48px;height:48px;margin:0 auto 12px}
.footer-brand .name{font-size:22px;font-weight:600;color:var(--ink);white-space:nowrap}
.footer-col{position:absolute;top:3780px;font-size:14px;line-height:21px}
.footer-col h4{font-size:14px;font-weight:600;margin-bottom:6px}
.socials{display:flex;gap:8px;margin-top:8px}
.socials span{width:20px;height:20px;background:var(--red);border-radius:3px}
.copyright-line{position:absolute;left:0;top:3998px;width:1200px;height:1px;background:#ccc}
.copyright{position:absolute;left:0;top:4010px;width:1200px;text-align:center;font-size:14px}
</style>
</head>
<body>

<header class="site-header">
  <div class="brand"><span class="brand-mark"></span><span class="brand-name">Brightpath</span></div>
  <nav class="main-nav"><span>Job Seekers</span><span>Hire Talent</span><span>Insights</span><span>Explore Consulting Solutions</span><span>About Us</span></nav>
  <div class="login">Login</div>
</header>

<section class="hero" role="img" aria-label="Team of professionals reviewing charts together with a glowing network graphic">
  <h1 class="hero-title heading">Search Jobs through Brightpath</h1>
  <div class="hero-label" style="left:37px">Search for</div>
  <div class="hero-label" style="left:438px">Where?</div>
  <div class="hero-input" style="left:37px;width:333px">Job title or keyword</div>
  <div class="hero-input" style="left:378px;width:333px">Location or zip code</div>
  <div class="hero-btn">Find A Job</div>
  <div class="hero-opt" style="left:40px">
    <svg width="26" height="24" viewBox="0 0 26 24"><path d="M2 11 24 2 15 22 12 13Z" fill="#fff"/></svg>Use current location</div>
  <div class="hero-opt" style="left:378px"><span class="checkbox"></span>Remote jobs only</div>
</section>

<nav class="tabs"><span>Jobs by Industry</span><span>Jobs by State</span><span>Jobs by Type</span><span>Jobs by Featured Companies</span></nav>

<div class="industry" style="left:70px;top:820px"><span class="ic"></span><span class="txt">Accounting &amp; Finance</span></div>
<div class="industry" style="left:70px;top:853px"><span class="ic"></span><span class="txt">Call Center &amp; Customer Service</span></div>
<div class="industry" style="left:70px;top:886px"><span class="ic"></span><span class="txt">Creative &amp; Marketing</span></div>
<div class="industry" style="left:70px;top:920px"><span class="ic"></span><span class="txt">Engineering &amp; Technology</span></div>
<div class="industry" style="left:446px;top:820px"><span class="ic"></span><span class="txt">Hospitality</span></div>
<div class="industry" style="left:446px;top:853px"><span class="ic"></span><span class="txt">Human Resources</span></div>
<div class="industry" style="left:446px;top:886px"><span class="ic"></span><span class="txt">Industrial &amp; Manufacturing</span></div>
<div class="industry" style="left:446px;top:920px"><span class="ic"></span><span class="txt">Medical &amp; Science</span></div>
<div class="industry" style="left:790px;top:820px;width:320px"><span class="ic"></span><span class="txt" style="width:286px">Office, Clerical, &amp; Administrative</span></div>
<div class="industry" style="left:790px;top:853px;width:320px"><span class="ic"></span><span class="txt" style="width:286px">Retail</span></div>
<div class="industry" style="left:790px;top:886px;width:320px"><span class="ic"></span><span class="txt" style="width:286px">Transportation</span></div>
<div class="industry" style="left:790px;top:920px;width:320px"><span class="ic"></span><span class="txt" style="width:286px">Warehousing</span></div>

<svg class="abs" style="left:0;top:0" width="1200" height="1000" aria-hidden="true">
  <g stroke="#c01e2e" stroke-width="1.6" fill="none">
    <path d="M368 832h24m-5-4 5 4-5 4M368 865h24m-5-4 5 4-5 4M368 898h24m-5-4 5 4-5 4M368 932h24m-5-4 5 4-5 4"/>
    <path d="M712 829h24m-5-4 5 4-5 4M712 862h24m-5-4 5 4-5 4M712 895h24m-5-4 5 4-5 4M712 929h24m-5-4 5 4-5 4"/>
    <path d="M1104 829h24m-5-4 5 4-5 4M1104 862h24m-5-4 5 4-5 4M1104 895h24m-5-4 5 4-5 4M1104 929h24m-5-4 5 4-5 4"/>
  </g>
</svg>

<h2 class="how-title heading">How it works</h2>
<div class="connector" style="left:340px;width:69px"></div>
<div class="connector" style="left:744px;width:70px"></div>
<div class="step" style="left:74px;width:266px">Describe your need</div>
<div class="step" style="left:409px;width:335px">View matching candidates</div>
<div class="step" style="left:814px;width:332px">Connect with a recruiter to<br>consult and hire</div>
<div class="step-num" style="left:55px">1</div>
<div class="step-num" style="left:390px">2</div>
<div class="step-num" style="left:795px">3</div>

<section class="jobs-band"></section>
<h2 class="jobs-title heading">Latest Job</h2>

<article class="job-card" style="left:41px">
  <div class="job-added">Added today</div>
  <h3 class="job-title">Registered Nurse</h3>
  <p class="job-desc">Tomval Medical &amp; Science is looking for multiple Registered Nurses for our client in Seattle, WA ! Please review details below and apply with a current resume for consideration ...</p>
  <div class="job-meta" style="top:254px"><svg width="14" height="18" viewBox="0 0 14 18"><path d="M7 0a7 7 0 0 0-7 7c0 5 7 11 7 11s7-6 7-11a7 7 0 0 0-7-7Zm0 10a3 3 0 1 1 0-6 3 3 0 0 1 0 6Z" fill="#c01e2e"/></svg>Seattle, Washington</div>
  <div class="job-meta" style="top:285px"><svg width="18" height="16" viewBox="0 0 18 16"><rect y="3" width="18" height="13" rx="2" fill="#c01e2e"/><rect x="6" width="6" height="4" fill="none" stroke="#c01e2e" stroke-width="2"/></svg>$45 - $47.3</div>
  <div class="job-btn">See Job Description</div>
  <svg class="bookmark" width="22" height="36" viewBox="0 0 22 36"><path d="M2 2h18v32l-9-8-9 8Z" fill="none" stroke="#c01e2e" stroke-width="2.4"/></svg>
</article>

<article class="job-card" style="left:422px">
  <div class="job-added">Added today</div>
  <h3 class="job-title">Maintenance Technician</h3>
  <p class="job-desc">$5000 sign-on bonus up to $25/hr after 1 week orientation We have partnered to recruit for Maintenance Generalists to troubleshoot, maintain, and repair equipment and ...</p>
  <div class="job-meta" style="top:254px"><svg width="14" height="18" viewBox="0 0 14 18"><path d="M7 0a7 7 0 0 0-7 7c0 5 7 11 7 11s7-6 7-11a7 7 0 0 0-7-7Zm0 10a3 3 0 1 1 0-6 3 3 0 0 1 0 6Z" fill="#c01e2e"/></svg>Waterloo, Iowa</div>
  <div class="job-meta" style="top:285px"><svg width="18" height="16" viewBox="0 0 18 16"><rect y="3" width="18" height="13" rx="2" fill="#c01e2e"/><rect x="6" width="6" height="4" fill="none" stroke="#c01e2e" stroke-width="2"/></svg>$24.50</div>
  <div class="job-btn">See Job Description</div>
  <svg class="bookmark" width="22" height="36" viewBox="0 0 22 36"><path d="M2 2h18v32l-9-8-9 8Z" fill="none" stroke="#c01e2e" stroke-width="2.4"/></svg>
</article>

<article class="job-card" style="left:803px">
  <div class="job-added">Added today</div>
  <h3 class="job-title">Medical Front Desk</h3>
  <p class="job-desc">Tomval is assisting our client in fulfilling a Front Desk support position located in San Antonio, 78233. This is an onsite position. If you meet the qualifications listed ...</p>
  <div class="job-meta" style="top:254px"><svg width="14" height="18" viewBox="0 0 14 18"><path d="M7 0a7 7 0 0 0-7 7c0 5 7 11 7 11s7-6 7-11a7 7 0 0 0-7-7Zm0 10a3 3 0 1 1 0-6 3 3 0 0 1 0 6Z" fill="#c01e2e"/></svg>San Antonio, Texas</div>
  <div class="job-meta" style="top:285px"><svg width="18" height="16" viewBox="0 0 18 16"><rect y="3" width="18" height="13" rx="2" fill="#c01e2e"/><rect x="6" width="6" height="4" fill="none" stroke="#c01e2e" stroke-width="2"/></svg>$15.00</div>
  <div class="job-btn">See Job Description</div>
  <svg class="bookmark" width="22" height="36" viewBox="0 0 22 36"><path d="M2 2h18v32l-9-8-9 8Z" fill="none" stroke="#c01e2e" stroke-width="2.4"/></svg>
</article>

<a class="see-more">See More Latest Job &gt;&gt;</a>

<section class="red-band" style="top:1951px;height:534px"></section>
<div class="frame" style="left:122px;top:2052px;width:355px;height:290px"></div>
<div class="photo" style="left:183px;top:2096px;width:355px;height:290px;background:linear-gradient(135deg,#d8d2c8,#6b5f55 55%,#2b2d33)" role="img" aria-label="Two businessmen in suits reviewing a tablet together"></div>
<h2 class="feature-title heading" style="left:588px;top:2035px">Consulting solutions<br>to drive business impact</h2>
<div class="check-item" style="left:588px;top:2160px"><svg width="30" height="28" viewBox="0 0 30 28"><rect x="1" y="3" width="24" height="24" rx="3" fill="#fff"/><path d="M6 14l6 6L28 3" fill="none" stroke="#c01e2e" stroke-width="3"/></svg><span>Develop a clear vision and strategy</span></div>
<div class="check-item" style="left:588px;top:2200px"><svg width="30" height="28" viewBox="0 0 30 28"><rect x="1" y="3" width="24" height="24" rx="3" fill="#fff"/><path d="M6 14l6 6L28 3" fill="none" stroke="#c01e2e" stroke-width="3"/></svg><span>Enhance business performance with critical<br>technologies and processes</span></div>
<div class="check-item" style="left:588px;top:2266px"><svg width="30" height="28" viewBox="0 0 30 28"><rect x="1" y="3" width="24" height="24" rx="3" fill="#fff"/><path d="M6 14l6 6L28 3" fill="none" stroke="#c01e2e" stroke-width="3"/></svg><span>Implement a plan or manage operations</span></div>
<div class="btn-white" style="left:588px;top:2337px;width:251px;font-size:18px">Find your consulting<br>solution</div>
<div class="btn-white" style="left:856px;top:2337px;width:154px;font-size:20px">Learn More</div>

<section class="red-band" style="top:2486px;height:602px;border-top:1.5px solid #d96a75"></section>
<h2 class="feature-title heading" style="left:122px;top:2570px">Make the career move<br>you want</h2>
<div class="check-item" style="left:122px;top:2694px"><svg width="30" height="28" viewBox="0 0 30 28"><rect x="1" y="3" width="24" height="24" rx="3" fill="#fff"/><path d="M6 14l6 6L28 3" fill="none" stroke="#c01e2e" stroke-width="3"/></svg><span>Get instant job recommendations tailored to<br>your skills and goals</span></div>
<div class="check-item" style="left:122px;top:2760px"><svg width="30" height="28" viewBox="0 0 30 28"><rect x="1" y="3" width="24" height="24" rx="3" fill="#fff"/><path d="M6 14l6 6L28 3" fill="none" stroke="#c01e2e" stroke-width="3"/></svg><span>Gain exposure to a range of companies and<br>job types: fully remote, hybrid or on-site, and<br>contract or permanent</span></div>
<div class="check-item" style="left:122px;top:2850px"><svg width="30" height="28" viewBox="0 0 30 28"><rect x="1" y="3" width="24" height="24" rx="3" fill="#fff"/><path d="M6 14l6 6L28 3" fill="none" stroke="#c01e2e" stroke-width="3"/></svg><span>Access competitive pay, benefits, and free<br>online training and development</span></div>
<div class="btn-white" style="left:122px;top:2938px;width:251px;font-size:18px">Get job matches</div>
<div class="btn-white" style="left:388px;top:2938px;width:155px;font-size:20px">Learn More</div>
<div class="frame" style="left:720px;top:2630px;width:356px;height:290px"></div>
<div class="photo" style="left:659px;top:2675px;width:355px;height:289px;background:linear-gradient(180deg,#dfe6ec,#b9c3cc 60%,#7f8a96)" role="img" aria-label="Group of job candidates seated in a row waiting for interviews"></div>

<h2 class="insights-title heading">Hiring trends and insights</h2>
<article class="insight" style="left:40px">
  <div class="photo" style="background:linear-gradient(135deg,#8fa0b3,#d5dbe2)" role="img" aria-label="Handshake across an office desk"></div>
  <h3>What jobs are in<br>demand?</h3>
  <p>Explore our Demand for Skilled Talent report to see what specializations</p>
  <div class="read">Read More</div>
</article>
<article class="insight" style="left:325px">
  <div class="photo" style="background:linear-gradient(135deg,#e5ddd2,#9a8a76)" role="img" aria-label="Smiling professional holding cash at a laptop"></div>
  <h3>2024 Salary Guide</h3>
  <p>Explore the latest data for 500-plus positions and know what you should</p>
  <div class="read">Read More</div>
</article>
<article class="insight" style="left:610px">
  <div class="photo" style="background:linear-gradient(135deg,#c9d3e0,#2a3d63)" role="img" aria-label="Diverse team of colleagues meeting in an office"></div>
  <h3>Multigenerational<br>Workforce Report</h3>
  <p>Learn how to better recruit, motivate and retain today's</p>
  <div class="read">Read More</div>
</article>
<article class="insight" style="left:895px">
  <div class="photo" style="background:linear-gradient(135deg,#0f2a3c,#2f6f86 60%,#123042)" role="img" aria-label="Hand touching a digital checkmark interface"></div>
  <h3>A Future-Proofed<br>Workforce</h3>
  <p>Get this 8-point plan to help your company craft a blueprint for adapting to</p>
  <div class="read">Read More</div>
</article>

<div class="footer-line"></div>
<div class="footer-brand"><div class="brand-mark"></div><div class="name">Brightpath</div></div>
<div class="footer-col" style="left:410px"><h4>Services</h4>Browse Jobs<br>Contract Talent<br>Permanent Talent<br>Consulting Solutions</div>
<div class="footer-col" style="left:680px"><h4>Resources &amp; Tools</h4>Discover Insights<br>Invoice<br>Job Directory<br>Salary Guide<br>Time Reports<br>Contact Us</div>
<div class="footer-col" style="left:940px"><h4>About Us</h4>About Brightpath<br>Leadership<br>Careers With Us<br>Locations<br>Investor Center<br>Press
  <div class="socials"><span></span><span></span><span></span><span></span></div></div>
<div class="copyright-line"></div>
<div class="copyright">© Copyright 2024 Brightpath Inc.</div>

</body>
</html>
```